Business Card Design for Property Development Company Director

I am looking for a professional and unforgettable business card design for our Director of our Property Development Company.
Please see attached .pptx file to find out what information to include. You don't have to follow the exact format shown in the file - I am interested to see your creative flair using the information provided.

```html
<!DOCTYPE html>
<html lang="en">
<head>
<meta charset="utf-8">
<title>Kestrel Property Group – Business Card</title>
<link href="https://fonts.googleapis.com/css2?family=Roboto:wght@400;500;700;900&display=swap" rel="stylesheet">
<style>
  :root {
    --blue: #1058a8;
    --grey: #5a5a5a;
    --ink: #111111;
    --paper: #ffffff;
    --backdrop: #2b2c2e;
  }
  * { box-sizing: border-box; margin: 0; padding: 0; }
  html, body { width: 1200px; height: 1200px; overflow: hidden; }
  body {
    background: var(--backdrop);
    font-family: "Roboto", Arial, sans-serif;
    display: flex;
    flex-direction: column;
    align-items: center;
    justify-content: center;
    gap: 56px;
  }
  .card {
    position: relative;
    width: 880px;
    height: 503px;
    background: var(--paper);
    border-radius: 34px;
    overflow: hidden;
  }
  .brand {
    display: flex;
    align-items: center;
    gap: 22px;
    color: var(--blue);
    font-weight: 700;
  }
  .brand-mark {
    width: 74px;
    height: 74px;
    background: var(--blue);
    flex: none;
  }
  .brand-name { line-height: 1; }
  .brand-name .line-1 { display: block; font-size: 64px; letter-spacing: 1px; }
  .brand-name .line-2 { display: block; font-size: 26px; letter-spacing: 11px; margin-top: 8px; }

  /* back */
  .card-back { display: flex; flex-direction: column; align-items: center; }
  .tagline {
    margin-top: 70px;
    text-align: center;
    color: var(--blue);
    font-weight: 700;
    font-size: 27px;
    line-height: 1.15;
    letter-spacing: 0.5px;
  }
  .card-back .brand { margin-top: 58px; }
  .invite {
    position: absolute;
    bottom: 52px;
    left: 0; right: 0;
    text-align: center;
    color: var(--grey);
    font-size: 22px;
    font-weight: 500;
  }
  .invite strong { color: var(--blue); font-weight: 500; }

  /* front */
  .card-front .brand { position: absolute; top: 58px; left: 50%; transform: translateX(-50%); }
  .contact-row {
    position: absolute;
    top: 262px;
    left: 110px;
    display: flex;
    align-items: center;
  }
  .person { text-align: right; padding-right: 24px; }
  .person-name { color: var(--blue); font-weight: 700; font-size: 36px; letter-spacing: -0.5px; }
  .person-role { color: var(--ink); font-size: 22px; margin-top: 2px; }
  .divider { width: 2px; height: 110px; background: var(--blue); }
  .details { list-style: none; padding-left: 24px; }
  .details li {
    display: flex; align-items: center; gap: 12px;
    font-size: 23px; color: var(--ink); line-height: 1.45;
  }
  .details svg { width: 20px; height: 20px; flex: none; }
  .licence-band {
    position: absolute;
    left: 0; right: 0; bottom: 0;
    height: 86px;
    background: var(--blue);
    color: var(--paper);
    font-size: 24px;
    font-weight: 500;
    display: flex;
    align-items: center;
    justify-content: center;
  }
</style>
</head>
<body>

  <section class="card card-back">
    <p class="tagline">Property Development<br>&amp; Site Acquisition Specialists</p>
    <div class="brand">
      <span class="brand-mark"></span>
      <span class="brand-name"><span class="line-1">KESTREL</span><span class="line-2">PROPERTY GROUP</span></span>
    </div>
    <p class="invite">Ask me about our <strong>INVESTMENT &amp; PARTNERSHIP</strong> opportunities</p>
  </section>

  <section class="card card-front">
    <div class="brand">
      <span class="brand-mark"></span>
      <span class="brand-name"><span class="line-1">KESTREL</span><span class="line-2">PROPERTY GROUP</span></span>
    </div>

    <div class="contact-row">
      <div class="person">
        <p class="person-name">Daniel Marsh</p>
        <p class="person-role">Director</p>
      </div>
      <span class="divider"></span>
      <ul class="details">
        <li>
          <svg viewBox="0 0 24 24" aria-hidden="true"><path fill="#1058a8" d="M6.6 10.8a15.1 15.1 0 0 0 6.6 6.6l2.2-2.2a1 1 0 0 1 1-.25 11.4 11.4 0 0 0 3.6.57 1 1 0 0 1 1 1V20a1 1 0 0 1-1 1A17 17 0 0 1 3 4a1 1 0 0 1 1-1h3.5a1 1 0 0 1 1 1c0 1.25.2 2.45.57 3.57a1 1 0 0 1-.25 1z"/></svg>
          0400 318 562
        </li>
        <li>
          <svg viewBox="0 0 24 24" aria-hidden="true"><rect x="2" y="5" width="20" height="14" rx="1" fill="none" stroke="#1058a8" stroke-width="2"/><path d="M2 6l10 7 10-7" fill="none" stroke="#1058a8" stroke-width="2"/></svg>
          daniel@kestrelpg.com.au
        </li>
        <li>
          <svg viewBox="0 0 24 24" aria-hidden="true"><g fill="none" stroke="#1058a8" stroke-width="1.8"><circle cx="12" cy="12" r="9.5"/><ellipse cx="12" cy="12" rx="4" ry="9.5"/><path d="M2.5 12h19M4 7h16M4 17h16"/></g></svg>
          www.kestrelpg.com.au
        </li>
      </ul>
    </div>

    <div class="licence-band">Real Estate Lic: 5102934 &amp; 5102935</div>
  </section>

</body>
</html>
```